CoinHarbor.com Site Redesign

We are looking to redesign our CoinHarbor.com site. This site is focused on helping consumers make smart financial decisions. We provide reviews and articles in various categories.

We are looking for a responsive design to run on wordpress. We will also have adsense advertisements on our page and will want some ad spot space. We are thinking of two column design vs. single column.

Here is an example of what our competitors look like:
ShopperBeacon.org (mostly reviews vs. articles)
Homepage - https://www.shopperbeacon.example/
Category Review Listing - https://www.shopperbeacon.example/mortgage-refinance/best-mortgage-refinance
Individual Review - https://www.shopperbeacon.example/mortgage-refinance/c/loan-orchard-mortgage-refinance-review

- I like that the site is extremely clean. I like the fixed header in mobile

PilotGuide
Homepage - https://www.pilotguide.example/
Category Review Listing-https://www.pilotguide.example/auto_insurance/index.php
Individual Review- https://www.pilotguide.example/auto_insurance/drivora_review.php

Articles - https://www.pilotguide.example/blog/2017/11/20/going-on-a-holiday-road-trip-be-prepared-for-these-hazards/

What I Like? I like the two column layout in that it gives room for advertising.
What I Do NOT Like? The top navigation is a little cumbersome and old. Mobile view is not very good. Content seems a bit cluttered.

PennyMoth
Homepage - https://www.pennymoth.example
Category Review Listing - https://www.pennymoth.example/blog/insurance/best-car-insurance-companies/?trk=pm_gn1_4.0
Individual Review- https://www.pennymoth.example/blog/insurance/veloro-insurance-review/

What I Like? very clean. Like the use of white space and focus on bright color call to action buttons.
What I Do NOT Like? In mobile a lot of content is pushed below the fold because of the large image above the fold. Reviews are not well organized.

Target Market(s)

consumers interested in saving money and making smart financial decisions

Industry/Entity Type

Financial

Logo Text

CoinHarbor.com or CoinHarbor

Coding

Coded - Design and coding required

Number of Pages Required

5+ page

Font styles to use
Sans Serif

Colors

Designer to choose colors to be used in the design.

Requirements
Must have
• -responsive design
• -room for ad space in the right column
Nice to have
• -good use of white space
• -clean layouts
Should not have
• -clutter

```html
<!DOCTYPE html>
<html lang="en">
<head>
<meta charset="utf-8">
<title>CoinHarbor.com – Make smarter financial decisions</title>
<link href="https://fonts.googleapis.com/css2?family=Open+Sans:wght@400;600;700;800&display=swap" rel="stylesheet">
<style>
:root{
  --navy:#0b2072;
  --navy-dark:#091a5e;
  --blue:#1f4fa8;
  --text:#222;
  --muted:#666;
  --line:#cfd3dc;
  --white:#fff;
}
*{box-sizing:border-box;margin:0;padding:0}
html,body{width:1200px;height:2731px;overflow:hidden;background:var(--white)}
body{position:relative;font-family:"Open Sans",Arial,sans-serif;color:var(--text)}
.abs{position:absolute}
a{color:inherit;text-decoration:none}

/* top bar */
.topbar{left:0;top:0;width:1200px;height:22px;background:var(--navy);color:var(--white);font-size:14px;font-weight:600}
.topbar .contact{left:100px;top:2px;display:flex;gap:28px}
.topbar .contact span{display:flex;align-items:center;gap:8px}
.topbar .login{right:100px;top:2px;display:flex;align-items:center;gap:8px}

/* header */
.header{left:0;top:22px;width:1200px;height:69px;background:var(--white)}
.logo{left:100px;top:20px;display:flex;align-items:center;gap:8px;font-size:23px;font-weight:700;color:var(--navy)}
.logo .mark{width:26px;height:26px;background:var(--navy)}
.nav{right:98px;top:26px;display:flex;gap:20px;font-size:15px;font-weight:600;color:#111;align-items:center}
.nav .active{color:var(--blue)}

/* hero */
.hero{left:0;top:91px;width:1200px;height:593px;background:linear-gradient(100deg,#2d3f52 0%,#55708a 35%,#8aa0b4 60%,#c9c4c0 80%,#2a2a30 100%)}
.hero-title{left:97px;top:212px;font-size:54px;font-weight:800;color:var(--white);letter-spacing:1px}
.hero-sub{left:98px;top:278px;font-size:34px;font-weight:600;color:var(--white)}
.search{left:100px;top:344px;width:636px;height:42px;display:flex;border:2px solid var(--white)}
.search .field{flex:1;font-size:13px;color:#eee;padding:10px 20px;background:rgba(255,255,255,.08)}
.search .btn{width:156px;background:var(--navy);color:var(--white);font-weight:700;font-size:17px;display:flex;align-items:center;justify-content:center;border-left:2px solid var(--white)}
.dots{left:580px;top:598px;display:flex;gap:6px}
.dots i{width:10px;height:10px;border-radius:50%;border:1.5px solid var(--white);display:block}
.dots i.on{background:var(--white)}

/* finder */
.finder{left:250px;top:754px;display:flex;align-items:center;gap:22px;font-size:18px;font-weight:700}
.finder .pick{width:173px;height:38px;background:var(--navy);color:var(--white);font-size:15px;font-weight:400;display:flex;align-items:center;justify-content:center}

/* categories */
.cat{width:201px;height:137px;display:flex;align-items:center;justify-content:center;color:var(--white);font-weight:700;font-size:15px;text-shadow:0 1px 3px rgba(0,0,0,.6)}
.c1{background:linear-gradient(135deg,#a0917a,#6d6556)}
.c2{background:linear-gradient(135deg,#8a7a66,#4f4a44)}
.c3{background:linear-gradient(135deg,#3a3a3e,#151517)}
.c4{background:linear-gradient(135deg,#b89a7a,#6e5a48)}
.c5{background:linear-gradient(135deg,#5e5a56,#2f2c2a)}
.c6{background:linear-gradient(135deg,#4a4a4e,#222226)}
.c7{background:linear-gradient(135deg,#6f96b0,#a88466)}
.c8{background:linear-gradient(135deg,#7c7a76,#3e3b38)}
.c9{background:linear-gradient(135deg,#6a6864,#2d2b29)}

/* sidebar */
.about-box{left:770px;top:818px;width:330px}
.about-box h2{font-size:21px;font-weight:700;text-align:center}
.about-box .tag{font-size:13px;color:#444;text-align:center;margin-top:6px}
.feature{margin:22px 12px 0;padding-bottom:22px;border-bottom:1.5px solid #888}
.feature h3{font-size:16px;font-weight:600;display:flex;justify-content:space-between;align-items:center}
.feature p{font-size:13px;color:var(--muted);line-height:23px;margin-top:14px}
.ad{left:770px;width:330px;height:200px}
.ad1{top:1213px;background:linear-gradient(90deg,#e8a23c 0%,#e39a30 60%,#3a4552 62%,#56606c 100%)}
.ad2{top:1460px;background:linear-gradient(135deg,#9aa2ac,#5d6670 60%,#8c2418)}
.ad3{top:1708px;background:linear-gradient(180deg,#2f63b8 0%,#3f7ad0 60%,#f2c51e 75%,#e8b814 100%)}

/* articles */
.section-title{left:98px;top:1320px;width:629px;text-align:center;font-size:30px;font-weight:700}
.card{width:294px;height:392px;border:1px solid #dcdcdc;background:var(--white)}
.card .photo{height:196px}
.card .avatar{position:absolute;left:125px;top:174px;width:44px;height:44px;border-radius:50%;border:3px solid var(--white);background:#c9a68a}
.card h4{position:absolute;left:33px;top:232px;width:240px;font-size:18px;font-weight:700;line-height:24px}
.card p{position:absolute;left:36px;top:282px;width:226px;font-size:13.5px;color:var(--muted);line-height:23px}
.card .foot{position:absolute;left:31px;top:353px;width:245px;display:flex;justify-content:space-between;align-items:center}
.card .more{font-size:14px;font-weight:600;color:var(--navy)}
.card .meta{font-size:8px;color:#555}
.p1{background:linear-gradient(135deg,#dfe6ee,#5b7ea8 60%,#c8ced6)}
.p2{background:linear-gradient(180deg,#a3ab9c,#6d7066 55%,#8d8d86)}
.p3{background:linear-gradient(135deg,#3c3f44,#121316 60%,#6a6d72)}
.p4{background:linear-gradient(180deg,#a8c4de,#6f8f5e 55%,#4d6f9a)}
.btn-more{left:342px;top:2267px;width:142px;height:44px;background:var(--navy);color:var(--white);font-size:13px;font-weight:700;display:flex;align-items:center;justify-content:center;letter-spacing:.5px}

/* footer */
.footer{left:0;top:2377px;width:1200px;height:354px;background:var(--navy-dark);color:var(--white)}
.footer h5{font-size:20px;font-weight:600;letter-spacing:.5px}
.f-about{left:98px;top:52px;width:210px}
.f-about p{font-size:12px;line-height:23px;margin-top:22px;text-align:justify}
.f-services{left:351px;top:52px;width:430px}
.f-services ul{list-style:none;display:grid;grid-template-columns:141px 149px 140px;margin-top:24px;row-gap:7px}
.f-services li{font-size:12px}
.f-services li::before{content:"›";margin-right:12px}
.f-sub{left:838px;top:52px;width:262px}
.f-sub p{font-size:12px;line-height:23px;margin-top:20px}
.f-sub form{display:flex;margin-top:20px;height:36px}
.f-sub .mail{flex:1;border:1px solid var(--white);font-size:12px;padding:9px 10px}
.f-sub .go{width:110px;background:var(--white);color:var(--text);font-size:12px;font-weight:700;display:flex;align-items:center;justify-content:center}
.social{left:98px;top:222px;display:flex;gap:8px}
.social i{width:34px;height:34px;border-radius:50%;border:1.5px solid var(--white);display:block}
.f-line{left:98px;top:285px;width:1002px;height:1px;background:#7b86b4}
.copy{left:0;top:312px;width:1200px;text-align:center;font-size:12px}
</style>
</head>
<body>

<div class="abs topbar">
  <div class="abs contact">
    <span><svg width="12" height="12" viewBox="0 0 24 24"><path fill="#fff" d="M6.6 10.8a15 15 0 0 0 6.6 6.6l2.2-2.2c.3-.3.7-.4 1-.2 1.1.4 2.3.6 3.6.6.6 0 1 .4 1 1V20c0 .6-.4 1-1 1A17 17 0 0 1 3 4c0-.6.4-1 1-1h3.5c.6 0 1 .4 1 1 0 1.3.2 2.5.6 3.6.1.3 0 .7-.2 1z"/></svg>+1-555-010-0199</span>
    <span><svg width="13" height="10" viewBox="0 0 26 20"><path fill="#fff" d="M0 0h26v20H0z"/><path d="M0 1l13 10L26 1" stroke="#0b2072" stroke-width="2.5" fill="none"/></svg>info@coinharbor.example</span>
  </div>
  <div class="abs login">LOG IN <svg width="10" height="12" viewBox="0 0 10 12"><rect x="0" y="5" width="10" height="7" fill="#fff"/><path d="M2.5 5V3.5a2.5 2.5 0 0 1 5 0V5" stroke="#fff" stroke-width="1.6" fill="none"/></svg></div>
</div>

<header class="abs header">
  <div class="abs logo"><span class="mark"></span>CoinHarbor.com</div>
  <nav class="abs nav">
    <a class="active">Home</a><a>Annuities</a><a>Auto Insurance</a><a>Credit Monitoring</a><a>Debt Management</a><a>Mortgages</a>
    <svg width="16" height="16" viewBox="0 0 16 16"><circle cx="6.5" cy="6.5" r="5" stroke="#111" stroke-width="2.2" fill="none"/><path d="M10.5 10.5l4 4" stroke="#111" stroke-width="2.5"/></svg>
  </nav>
</header>

<section class="abs hero" role="img" aria-label="Smiling businesswoman giving a thumbs up in front of a blurred office team"></section>
<svg class="abs" style="left:0;top:91px" width="1200" height="593" viewBox="0 91 1200 593">
  <polygon points="0,537 601,672 1200,546 1200,552 601,686 0,540" fill="#0b2072"/>
  <polygon points="0,540 601,686 1200,552 1200,684 0,684" fill="#fff"/>
</svg>
<h1 class="abs hero-title">COINHARBOR</h1>
<p class="abs hero-sub">Make smarter financial decisions</p>
<div class="abs search"><div class="field">Enter your keyword</div><div class="btn">SEARCH</div></div>
<div class="abs dots"><i class="on"></i><i></i><i></i></div>

<div class="abs finder">I'm looking for <span class="pick">Product Or Category</span></div>

<div class="abs cat c1" style="left:98px;top:827px" role="img" aria-label="Stacks of coins">Annuities</div>
<div class="abs cat c2" style="left:313px;top:827px" role="img" aria-label="Insurance paperwork and toy car">Auto Insurance</div>
<div class="abs cat c3" style="left:526px;top:827px" role="img" aria-label="Laptop with credit card">Credit Monitoring</div>
<div class="abs cat c4" style="left:98px;top:978px" role="img" aria-label="Woman reviewing bills">Credit Repair</div>
<div class="abs cat c5" style="left:313px;top:978px" role="img" aria-label="Calculator and documents">Debt Management</div>
<div class="abs cat c6" style="left:526px;top:978px" role="img" aria-label="Hands on a keyboard">Identity Theft</div>
<div class="abs cat c7" style="left:98px;top:1127px" role="img" aria-label="Hands protecting a family figure">Life Insurance</div>
<div class="abs cat c8" style="left:313px;top:1127px" role="img" aria-label="Couple meeting an agent">Mortgages</div>
<div class="abs cat c9" style="left:526px;top:1127px" role="img" aria-label="Trader at a desk">Online Brokerages</div>

<aside class="abs about-box">
  <h2>What is CoinHarbor.com?</h2>
  <p class="tag">Financial Service Advice and Reviews</p>
  <div class="feature">
    <h3>We Analyze &amp; Explain <svg width="20" height="20" viewBox="0 0 16 16"><circle cx="6.5" cy="6.5" r="5" stroke="#1f4fa8" stroke-width="2.2" fill="none"/><path d="M10.5 10.5l4 4" stroke="#1f4fa8" stroke-width="2.6"/></svg></h3>
    <p>Lorem ipsum dolor sit amet, consectetur adipiscing elit, sed do eiusmod tempor incididunt ut labore et dolore magna aliqua. Ut enim ad minim veniam</p>
  </div>
  <div class="feature">
    <h3>We Review &amp; Rate <svg width="20" height="20" viewBox="0 0 24 24"><path fill="#1f4fa8" d="M12 1.5l3.2 7 7.6.7-5.8 5 1.8 7.4L12 17.8 5.2 21.6 7 14.2l-5.8-5 7.6-.7z"/></svg></h3>
    <p>Duis aute irure dolor in reprehenderit in voluptate velit esse cillum dolore eu fugiat nulla pariatu</p>
  </div>
</aside>
<div class="abs ad ad1" role="img" aria-label="Advertisement for the Harbor WP theme for consulting and financial advisors"></div>
<div class="abs ad ad2" role="img" aria-label="Advertisement for CleanGuard antibacterial soap"></div>
<div class="abs ad ad3" role="img" aria-label="Advertisement for FizzPop soda bottles"></div>

<h2 class="abs section-title">Recent Articles</h2>

<article class="abs card" style="left:98px;top:1397px">
  <div class="photo p1" role="img" aria-label="Tablet showing financial charts"></div>
  <div class="avatar" role="img" aria-label="Author portrait"></div>
  <h4>5 “Easy” Ways Parents Can Save $1000’s a Year</h4>
  <p>Parents, let’s face it – the high cost of raising children leaves us all needing a little extra money</p>
  <div class="foot"><a class="more">Read more »</a><span class="meta">Jun 23,2017 | 3 comments</span></div>
</article>
<article class="abs card" style="left:433px;top:1397px">
  <div class="photo p2" role="img" aria-label="Bicycle and helmet lying on a road"></div>
  <div class="avatar" role="img" aria-label="Author portrait"></div>
  <h4>Motorcycle Insurance Basics</h4>
  <p>Motorcycle insurance can be quite expensive; it can be the same amount as an auto</p>
  <div class="foot"><a class="more">Read more »</a><span class="meta">Jun 25,2017 | 5 comments</span></div>
</article>
<article class="abs card" style="left:98px;top:1834px">
  <div class="photo p3" role="img" aria-label="Close-up of a car tyre"></div>
  <div class="avatar" role="img" aria-label="Author portrait"></div>
  <h4>How Do I Get Cheap Auto Insurance?</h4>
  <p>If you’re looking for cheap auto insurance, then you aren’t alone. Many drivers regularly search</p>
  <div class="foot"><a class="more">Read more »</a><span class="meta">Jun 17,2017 | 6 comments</span></div>
</article>
<article class="abs card" style="left:433px;top:1834px">
  <div class="photo p4" role="img" aria-label="Two men discussing beside a damaged car"></div>
  <div class="avatar" role="img" aria-label="Author portrait"></div>
  <h4>LA Car Insurance Requirements</h4>
  <p>If you live in Louisiana you are no doubt aware that you have to carry LA auto insurance</p>
  <div class="foot"><a class="more">Read more »</a><span class="meta">Jun 15,2017 | 9 comments</span></div>
</article>

<a class="abs btn-more">MORE ARTICLES</a>

<footer class="abs footer">
  <div class="abs f-about">
    <h5>ABOUT</h5>
    <p>Lorem ipsum dolor sit amet, consectetur adipiscing elit, sed do eiusmod tempor incididunt ut labore et dolore magna aliqua.</p>
  </div>
  <div class="abs f-services">
    <h5>OUR SERVICES</h5>
    <ul>
      <li>Annuities</li><li>Auto Insurance</li><li>Credit Monitoring</li>
      <li>Credit Repair</li><li>Debt Management</li><li>Homeowners Insurance</li>
      <li>Identity Theft</li><li>Life Insurance</li><li>Mortgages</li>
      <li>Online Brokerages</li><li>Payday Loans</li><li>Personal Finance</li>
    </ul>
  </div>
  <div class="abs f-sub">
    <h5>SUBSCRIBE</h5>
    <p>Subscribe To Our Newsletter To Get The Latest Great Deals And Reviews</p>
    <form><span class="mail">Your mail</span><span class="go">SUBSCRIBE</span></form>
  </div>
  <div class="abs social" aria-label="Social links"><i></i><i></i><i></i></div>
  <div class="abs f-line"></div>
  <p class="abs copy">Copyright © 2017 CoinHarbor. All rights reserved</p>
</footer>

</body>
</html>
```